Corbeck Aluminium Design Upgrade

- This is for a layout design of the home page only. No coding required.

- The design should be based around the attached HPID (home page information design) I've attached both a JPEG of this
- Information only is in RED text. Copy to go on the design in BLACK text. Some instructions are in the HPID. Please be creative!
- The design needs to be clean and spacious
- Use the logo provided. Please use the colours from the logos in the website design.
- I've attached some images to use as examples to use for home page gallery
- The product logos (Pelvane, Trimbough etc) showed in the HPV can be googled for a higher quality image if required.
- The header can be changed/altered - just needs to have all information as per logo, along with the phone number.

- Expected standard of design examples: (Please DO NOT copy these exactly – they are just examples)
http://www.halden-works.example.nz/
http://www.plinthcove.example.nz/
http://www.dusofern.example.nz/

Width of content will be 1100 pixels when implemented as a web page. Header height (without nav bar) 150-160 pixels.

The winning PSD file will have to be provided as follows…
1. Canvas size of 2000px x 2000px - 72ppi in Adobe Photoshop (CS5 compatible)
2. Width of content section is 1100px wide - centered in the canvas
3. Any button rollovers/hovers in the PSD as hidden layers.
4. All fonts used must be Google fonts (except for the header fonts).
5. You will need to supply the chosen home page plus one example page (example page as a style guide for how all other pages will look). Example page is only the header and navigational bar at the top, an empty sector in the middle with a column (180 px wide) which can be left or right aligned which means the main sector is 920 pixels wide, and then the footer at the bottom of the page.

```html
<!DOCTYPE html>
<html lang="en">
<head>
<meta charset="utf-8">
<title>Corbeck Aluminium – Home</title>
<link href="https://fonts.googleapis.com/css2?family=Open+Sans:ital,wght@0,400;0,600;0,700;0,800;1,400;1,600&family=Arimo:wght@400&display=swap" rel="stylesheet">
<style>
:root{
  --ink:#232323;
  --charcoal:#343940;
  --brand-red:#e8251f;
  --brand-yellow:#f6e600;
  --brand-blue:#1a1a8c;
  --page:#ececec;
  --card:#ffffff;
  --footer:#c3c3c3;
  --muted:#555;
}
*{box-sizing:border-box;margin:0;padding:0}
html,body{width:1200px;height:1117px;overflow:hidden}
body{position:relative;font-family:"Open Sans",sans-serif;background:var(--page);color:var(--ink)}
.abs{position:absolute}

/* header */
.topline{left:0;top:0;width:1200px;height:3px;background:var(--brand-yellow)}
.header{left:0;top:3px;width:1200px;height:127px;background:var(--ink)}
.brand-name{left:270px;top:38px;color:#fff;font-weight:800;font-size:30px;line-height:1;letter-spacing:-.3px;white-space:nowrap}
.location{left:700px;top:19px;width:120px;text-align:right;color:#fff;font-size:10.5px;line-height:13px}
.phone{left:700px;top:52px;width:108px;text-align:right;color:#fff;font-weight:700;font-size:12.5px}
.tagline{left:576px;top:76px;width:220px;color:#fff;font-size:7.5px;font-weight:600;letter-spacing:.4px;text-transform:uppercase;white-space:nowrap}
.partner-name{left:806px;top:63px;width:124px;text-align:center;color:#fff;font-weight:700;font-size:17px;letter-spacing:2px}

/* nav */
.nav{left:270px;top:103px;width:660px;height:33px;background:linear-gradient(#fff,#e4e4e4);display:flex;align-items:center;justify-content:center;gap:4px;font-size:8.2px;color:#333;text-transform:uppercase;white-space:nowrap}
.nav a{color:inherit;text-decoration:none}
.nav a.current{font-weight:700;color:#111}
.nav .dot{font-size:7px}

/* hero */
.stage{left:0;top:130px;width:1200px;height:350px;background:linear-gradient(#fbfbfb,#ececec)}
.headline{left:0;top:158px;width:1200px;text-align:center;font-size:22.5px;font-weight:400;font-style:italic;color:#777}
.headline .style{color:var(--brand-red)}
.headline .func{color:var(--brand-blue)}
.headline .join{color:#333}
.hero-photo{left:270px;top:225px;width:660px;height:225px;background:linear-gradient(180deg,#6e7780 0%,#c9c7c2 35%,#dedbd5 60%,#5d8a2d 80%,#3f6a1d 100%);box-shadow:0 10px 12px -8px rgba(0,0,0,.45)}
.hero-title{left:290px;top:388px;color:#fff;font-size:31px;text-shadow:0 1px 3px rgba(0,0,0,.4)}
.quote{left:691px;top:212px;width:219px;height:202px;background:#e2e2e2;box-shadow:0 0 3px rgba(0,0,0,.3)}
.quote h2{position:absolute;left:0;top:16px;width:100%;text-align:center;font-weight:400;font-size:18px;letter-spacing:-.6px}
.quote p{position:absolute;left:0;top:38px;width:100%;text-align:center;font-size:9px}
.field{position:absolute;left:13px;width:194px;height:23px;background:#fff;border:1px solid #bbb;font-size:8px;color:#444;padding:6px}
.quote-btn{position:absolute;left:13px;top:166px;width:194px;height:24px;background:#000;color:#fff;font-weight:700;font-size:11.5px;text-align:center;line-height:24px}

/* suppliers */
.suppliers{left:0;top:480px;width:1200px;height:82px;background:#fff}
.supplier{position:absolute;top:30px;font-weight:700;font-size:11px;color:#222;white-space:nowrap}
.supplier-badge{position:absolute;left:741px;top:18px;width:46px;height:46px;border-radius:50%;border:2px solid #333}

/* service cards */
.card{background:var(--card);border:1px solid #d4d4d4;box-shadow:0 10px 10px -9px rgba(0,0,0,.45)}
.card h3{background:var(--charcoal);color:#fff;font-weight:600;font-size:11.5px;height:27px;line-height:27px;padding-left:11px}
.card .copy{padding:8px 10px;font-family:"Arimo",sans-serif;font-size:8.2px;line-height:15.2px;color:#333}
.card .copy p+p{margin-top:15px}

/* footer */
.footer{left:0;top:954px;width:1200px;height:134px;background:var(--footer)}
.foot-title{font-weight:700;font-size:11px;color:#3a3a3a}
.foot-list{font-size:8px;line-height:10.8px;color:#444;list-style:none}
.foot-text{font-size:8px;line-height:10.8px;color:#444}
.divider{width:1px;height:106px;background:#888}
.seal{left:782px;top:970px;width:72px;height:72px;border-radius:50%;background:radial-gradient(circle,#1c1c1c 52%,#d6a727 54%,#f3d46a 70%,#b88a1e 100%)}
.seal-note{left:734px;top:1053px;width:170px;text-align:center;font-size:7.6px;line-height:10.5px;color:#333}
.bottombar{left:0;top:1088px;width:1200px;height:29px;background:var(--ink);color:#ddd;font-size:8px}
.bottombar span{position:absolute;left:270px;top:9px}
</style>
</head>
<body>

<div class="abs topline"></div>
<header class="abs header"></header>
<div class="abs brand-name">CORBECK ALUMINIUM</div>
<div class="abs location">Upper Hutt<br>Wellington</div>
<div class="abs phone">(04) 555 0182</div>
<div class="abs tagline">Excellence in aluminium windows &amp; doors</div>
<div class="abs partner-name">PELVANE</div>

<div class="abs stage"></div>
<nav class="abs nav">
  <a class="current" href="#">Home</a><span class="dot">•</span>
  <a href="#">About Us</a><span class="dot">•</span>
  <a href="#">New Homes</a><span class="dot">•</span>
  <a href="#">Commercial</a><span class="dot">•</span>
  <a href="#">Replacement Joinery</a><span class="dot">•</span>
  <a href="#">Double Glazing</a><span class="dot">•</span>
  <a href="#">Conservatories</a><span class="dot">•</span>
  <a href="#">Gallery</a><span class="dot">•</span>
  <a href="#">Free Quote</a><span class="dot">•</span>
  <a href="#">Contact</a>
</nav>

<h1 class="abs headline"><span class="style">Ensuring Style</span> and <span class="func">Functionality</span> with Your <span class="join">Alumininum Joinery</span></h1>

<div class="abs hero-photo" role="img" aria-label="Photo of a white commercial building with aluminium bay windows above a green hedge"></div>
<div class="abs hero-title">Commercial Joinery</div>

<form class="abs quote">
  <h2>GET A FREE QUOTE</h2>
  <p>FOR YOUR JOINERY NEEDS</p>
  <div class="field" style="top:60px">Your Name</div>
  <div class="field" style="top:95px">Phone Number</div>
  <div class="field" style="top:130px">Email Address</div>
  <div class="quote-btn">GET QUOTE</div>
</form>

<section class="abs suppliers">
  <span class="supplier" style="left:276px">PELVANE</span>
  <span class="supplier" style="left:386px">KESTRAL SERIES</span>
  <span class="supplier" style="left:534px">TRIMBOUGH</span>
  <span class="supplier" style="left:646px">VANTOR CORE</span>
  <span class="supplier-badge"></span>
  <span class="supplier" style="left:822px">ORLIN GLASSWORKS</span>
</section>

<article class="abs card" style="left:270px;top:587px;width:204px;height:177px">
  <h3>New Homes</h3>
  <div class="copy"><p>Building your dream home?</p><p>Corbeck Aluminium can provide a wide range of stylish and functional options to help you get your dream home.</p><p>From glass sliding doors to aluminium team will work closely with you to ensure you get the best result for your new home.</p></div>
</article>
<article class="abs card" style="left:498px;top:587px;width:204px;height:177px">
  <h3>Commercial</h3>
  <div class="copy"><p>Building your dream home?</p><p>Corbeck Aluminium can provide a wide range of stylish and functional options to help you get your dream home.</p><p>From glass sliding doors to aluminium team will work closely with you to ensure you get the best result for your new home.</p></div>
</article>
<article class="abs card" style="left:726px;top:587px;width:204px;height:177px">
  <h3>Replacement Joinery</h3>
  <div class="copy"><p>Building your dream home?</p><p>Corbeck Aluminium can provide a wide range of stylish and functional options to help you get your dream home.</p><p>From glass sliding doors to aluminium team will work closely with you to ensure you get the best result for your new home.</p></div>
</article>
<article class="abs card" style="left:270px;top:784px;width:319px;height:147px">
  <h3>Double Glazing</h3>
  <div class="copy"><p>Building your dream home?</p><p>Corbeck Aluminium can provide a wide range of stylish and functional options to help you get your dream home.</p><p>From glass sliding doors to aluminium team will work closely with you to ensure you get the best result for your new home.</p></div>
</article>
<article class="abs card" style="left:610px;top:784px;width:320px;height:147px">
  <h3>Conservatories</h3>
  <div class="copy"><p>Building your dream home?</p><p>Corbeck Aluminium can provide a wide range of stylish and functional options to help you get your dream home.</p><p>From glass sliding doors to aluminium team will work closely with you to ensure you get the best result for your new home.</p></div>
</article>

<footer class="abs footer"></footer>
<div class="abs foot-title" style="left:291px;top:970px">NAVIGATION</div>
<ul class="abs foot-list" style="left:291px;top:990px"><li>Home</li><li>About</li><li>Testimonials</li><li>New homes</li><li>Commercial</li><li>Replacement Joinery</li></ul>
<ul class="abs foot-list" style="left:382px;top:990px"><li>Double Glazing</li><li>Conservatories</li><li>Gallery</li><li>Free Quote</li><li>Contact</li></ul>
<div class="abs divider" style="left:463px;top:968px"></div>
<div class="abs foot-title" style="left:486px;top:970px">CONTACT DETAILS</div>
<div class="abs foot-text" style="left:487px;top:990px;width:180px">Physical Address: 14 Ferngate Cres, Upper Hutt<br><br>Tel: +04 555 0182<br>Fax: +04 555 0197<br><br>Postal Address: PO Box 40117, Upper Hutt</div>
<div class="abs divider" style="left:706px;top:968px"></div>
<div class="abs seal" role="img" aria-label="Gold money back guarantee seal"></div>
<div class="abs seal-note">We guarantee all our work. If there is ever a problem, we will be back to provide a solution</div>

<div class="abs bottombar"><span>Copyright © 2014 Corbeck Aluminium. All Rights Reserved.</span></div>

</body>
</html>
```